Modern Verdell Tree Care Website

I need a website for a full service Tree Care company. The company provides tree pruning, tree removal, tree preservation, emergency services, stump grinding, and emergency tree services.

Target Market(s)

Customers that need tree services

Industry/Entity Type

Landscaping, Tree Services

Coding

Coded - Design and coding required

Number of Pages Required

5+ page

Font styles to use
Sans Serif

Requirements
Must have
• Good clean design that showcases the services the company provides.
Nice to have
• Services page; contact form, blog, home page, about page

```html
<!DOCTYPE html>
<html lang="en">
<head>
<meta charset="UTF-8">
<title>Verdell Tree Care</title>
<link href="https://fonts.googleapis.com/css2?family=Manrope:wght@400;500;600;700&display=swap" rel="stylesheet">
<style>
:root{
  --green:#7cc242;
  --green-soft:#e8f3dc;
  --ink:#1d1d1d;
  --muted:#5c5c5c;
  --charcoal:#2b2b2b;
  --forest:#2d4a22;
  --white:#ffffff;
  --line:#cfcfcf;
}
*{box-sizing:border-box;margin:0;padding:0}
html,body{width:1200px;height:4785px;overflow:hidden}
body{font-family:"Manrope",sans-serif;color:var(--ink);background:var(--white);position:relative}
.abs{position:absolute}
.label{font-size:15px;color:var(--green);font-weight:500}
.h2{font-size:33px;line-height:45px;font-weight:500;letter-spacing:-.3px}
.btn{position:absolute;display:flex;align-items:center;justify-content:center;gap:10px;height:42px;border-radius:21px;background:var(--green);color:var(--white);font-size:13px;font-weight:500}
.btn svg{width:12px;height:12px}
.photo{position:absolute;border-radius:22px}
/* nav */
.nav a{position:absolute;top:31px;font-size:15px;font-weight:500;color:var(--ink);text-decoration:none}
.brand{position:absolute;left:530px;top:22px;display:flex;align-items:center;gap:10px}
.brand .mark{width:26px;height:26px;background:var(--green)}
.brand span{font-size:24px;font-weight:700;color:var(--charcoal);letter-spacing:1px}
/* hero */
.hero-title{position:absolute;left:67px;width:1066px;top:198px;text-align:center;color:var(--white);font-size:60px;line-height:74px;font-weight:600}
/* why */
.why{position:absolute;left:0;top:1391px;width:1200px;height:787px;background:var(--charcoal);border-radius:24px;color:var(--white)}
.card{position:absolute;left:117px;top:1680px;width:306px;height:313px;background:var(--white);border-radius:14px}
.card ul{position:absolute;left:50px;top:134px;list-style:disc;font-size:14.5px;line-height:22.5px;color:var(--muted)}
/* services */
.ghost{position:absolute;left:455px;top:2330px;font-size:165px;font-weight:700;color:var(--green-soft);letter-spacing:2px;white-space:nowrap;width:745px;overflow:hidden}
.pill{position:absolute;width:338px;height:56px;border:1.5px solid var(--line);border-radius:28px;display:flex;align-items:center;padding-left:26px;font-size:18px;font-weight:500}
.pill b{font-weight:400;color:#8a8a8a;margin-right:8px}
.pill i{position:absolute;right:12px;top:10px;width:34px;height:34px;border-radius:50%;border:1.5px solid var(--green);display:flex;align-items:center;justify-content:center}
.pill i svg{width:11px;height:11px}
.pill.active{background:var(--green);border-color:var(--green);color:var(--white)}
.pill.active b{color:var(--white)}
.pill.active i{border-color:var(--white)}
/* testimonials */
.testi{position:absolute;left:67px;top:3302px;width:1066px;height:483px;background:var(--forest);border-radius:28px;color:var(--white)}
/* blog */
.post p{position:absolute;font-size:14.5px;line-height:22px;width:338px}
.post a{position:absolute;font-size:12px;color:var(--green);text-decoration:none}
/* footer */
footer{position:absolute;left:0;top:4445px;width:1200px;height:340px;background:var(--forest);color:var(--white)}
footer h4{position:absolute;font-size:16px;font-weight:500}
footer .col a{display:block;font-size:13px;color:var(--white);text-decoration:none;line-height:31px}
.social{position:absolute;top:281px;width:20px;height:20px;border-radius:50%;border:2px solid var(--white)}
</style>
</head>
<body>

<header class="nav">
  <div class="abs" style="left:116px;top:0;width:46px;height:4px;background:var(--green)"></div>
  <a style="left:67px">Home</a>
  <a style="left:135px">About Us</a>
  <a style="left:227px">Services</a>
  <a style="left:314px">Blog</a>
  <div class="brand"><div class="mark"></div><span>VERDELL</span></div>
  <div class="btn" style="left:1012px;top:20px;width:121px;height:42px">Contact Us</div>
</header>

<section>
  <div class="photo" role="img" aria-label="Large leafy tree in front of a pale green apartment building" style="left:67px;top:82px;width:1066px;height:516px;background:linear-gradient(180deg,#6f8f4a 0%,#3e6a24 55%,#2f5418 100%)"></div>
  <h1 class="hero-title">Trusted Tree Care Services for<br>Your Needs</h1>
  <div class="btn" style="left:519px;top:392px;width:162px">Get Started
    <svg viewBox="0 0 12 12"><path d="M2 10L10 2M4 2h6v6" stroke="#fff" stroke-width="1.5" fill="none"/></svg></div>
</section>

<section>
  <div class="label abs" style="left:67px;top:666px">About Us</div>
  <h2 class="h2 abs" style="left:67px;top:698px;width:400px">A Dedicated Team Committed to Greener Spaces</h2>
  <div class="photo" role="img" aria-label="Arborist in a sun hat tending a leafy shrub" style="left:67px;top:882px;width:429px;height:234px;background:linear-gradient(120deg,#8aa85a,#566f34 60%,#b58a4e)"></div>
  <p class="abs" style="left:67px;top:1144px;width:430px;font-size:14.5px;line-height:22.5px;color:var(--muted)">Lorem ipsum dolor sit amet consectetur. Arcu ultricies viverra orci tellus sit sed elit vestibulum. Consectetur adipiscing faucibus in adipiscing non pellentesque nam placerat amet. Nunc dui urna erat ante. Donec dolor scelerisque amet commodo sapien eget in mattis vel.</p>
  <div class="btn" style="left:67px;top:1283px;width:175px">See About Us
    <svg viewBox="0 0 12 12"><path d="M2 10L10 2M4 2h6v6" stroke="#fff" stroke-width="1.5" fill="none"/></svg></div>
  <div class="photo" role="img" aria-label="Sculpted tree beside a green building under a blue sky" style="left:613px;top:665px;width:520px;height:590px;background:linear-gradient(180deg,#3aa6d8 0%,#7fb8c9 30%,#a3ad7a 55%,#3f6b2a 100%)"></div>
</section>

<section class="why">
  <div class="label abs" style="left:67px;top:78px">Why Choose Us</div>
  <h2 class="h2 abs" style="left:67px;top:100px;width:470px">The Best Choice for Your Tree Care Needs</h2>
  <p class="abs" style="left:704px;top:135px;width:430px;font-size:12px;line-height:18px;color:#e6e6e6">Lorem ipsum dolor sit amet consectetur. Arcu ultricies viverra orci tellus sit sed elit vestibulum. Consectetur adipiscing faucibus in adipiscing non pellentesque nam placerat amet.</p>
</section>
<div class="photo" role="img" aria-label="Ivy-covered brick building surrounded by trees" style="left:67px;top:1630px;width:1066px;height:481px;background:linear-gradient(110deg,#4c6a2c,#6d7a48 45%,#8a7a5a 70%,#556b33)"></div>
<div class="card">
  <div class="abs" role="img" aria-label="Two arborists standing among trees" style="left:26px;top:26px;width:170px;height:80px;border-radius:10px;background:linear-gradient(90deg,#8b9a6a,#5f7a48)"></div>
  <ul>
    <li>Licensed an Insured</li>
    <li>24-Hours Emergency Services</li>
    <li>Locally Owned &amp; Operated</li>
    <li>Professional Work</li>
    <li>Safety is Our No.1 Priority</li>
    <li>Free Estimates</li>
    <li>Licensed Arborist on Staff</li>
  </ul>
</div>

<section>
  <div class="label abs" style="left:67px;top:2248px">Services</div>
  <h2 class="h2 abs" style="left:67px;top:2280px;width:460px">Expert Solutions for All Your Tree Care Needs</h2>
  <p class="abs" style="left:702px;top:2312px;width:432px;font-size:12px;line-height:18px;color:var(--muted)">Lorem ipsum dolor sit amet consectetur. Arcu ultricies viverra orci tellus sit sed elit vestibulum. Consectetur adipiscing faucibus in adipiscing non pellentesque nam placerat amet.</p>
  <div class="ghost">SERVICES</div>
  <div class="photo" role="img" aria-label="Gardener pruning a flowering shrub" style="left:67px;top:2418px;width:338px;height:223px;background:linear-gradient(130deg,#3f6a2a,#6f8f4f 50%,#2f4f1e)"></div>
  <div class="abs" style="left:67px;top:2670px;font-size:34px;color:#f0a020">04</div>
  <div class="abs" style="left:67px;top:2722px;width:340px;font-size:18px;line-height:26px;font-weight:500">Expert Pruning for Healthier, More Beautiful Trees</div>
  <p class="abs" style="left:67px;top:2790px;width:320px;font-size:14.5px;line-height:22.5px;color:var(--muted)">Lorem ipsum dolor sit amet consectetur. Arcu ultricies viverra orci tellus sit sed elit vestibulum.</p>

  <div class="pill" style="left:431px;top:2512px"><b>01</b>Tree Trimming<i><svg viewBox="0 0 12 12"><path d="M2 10L10 2M4 2h6v6" stroke="#1d1d1d" stroke-width="1.5" fill="none"/></svg></i></div>
  <div class="pill" style="left:431px;top:2584px"><b>02</b>Tree Removal<i><svg viewBox="0 0 12 12"><path d="M2 10L10 2M4 2h6v6" stroke="#1d1d1d" stroke-width="1.5" fill="none"/></svg></i></div>
  <div class="pill" style="left:431px;top:2656px"><b>03</b>Tree Clearing<i><svg viewBox="0 0 12 12"><path d="M2 10L10 2M4 2h6v6" stroke="#1d1d1d" stroke-width="1.5" fill="none"/></svg></i></div>
  <div class="pill active" style="left:431px;top:2728px"><b>04</b>Tree Pruning<i><svg viewBox="0 0 12 12"><path d="M2 10L10 2M4 2h6v6" stroke="#fff" stroke-width="1.5" fill="none"/></svg></i></div>
  <div class="pill" style="left:431px;top:2800px"><b>05</b>Stump Grinding<i><svg viewBox="0 0 12 12"><path d="M2 10L10 2M4 2h6v6" stroke="#1d1d1d" stroke-width="1.5" fill="none"/></svg></i></div>
  <div class="pill" style="left:795px;top:2512px"><b>06</b>Tree Preservation<i><svg viewBox="0 0 12 12"><path d="M2 10L10 2M4 2h6v6" stroke="#1d1d1d" stroke-width="1.5" fill="none"/></svg></i></div>
  <div class="pill" style="left:795px;top:2584px"><b>07</b>Storm Damage CleanUp<i><svg viewBox="0 0 12 12"><path d="M2 10L10 2M4 2h6v6" stroke="#1d1d1d" stroke-width="1.5" fill="none"/></svg></i></div>
  <div class="pill" style="left:795px;top:2656px"><b>08</b>Emergency Tree<i><svg viewBox="0 0 12 12"><path d="M2 10L10 2M4 2h6v6" stroke="#1d1d1d" stroke-width="1.5" fill="none"/></svg></i></div>
  <div class="pill" style="left:795px;top:2728px"><b>09</b>Cabling &amp; Bracing<i><svg viewBox="0 0 12 12"><path d="M2 10L10 2M4 2h6v6" stroke="#1d1d1d" stroke-width="1.5" fill="none"/></svg></i></div>
</section>

<section>
  <div class="abs" role="img" aria-label="Team meeting with clients around a table in a bright office" style="left:0;top:2923px;width:1200px;height:310px;background:linear-gradient(90deg,#4a4a36,#5d6a4e 50%,#3f4a36)"></div>
  <div class="abs" style="left:0;top:2923px;width:1200px;height:310px;background:rgba(35,55,25,.45)"></div>
  <h2 class="h2 abs" style="left:0;width:1200px;top:2975px;text-align:center;color:var(--white)">Get in Touch with Verdell Tree Care</h2>
  <p class="abs" style="left:230px;width:740px;top:3050px;text-align:center;font-size:14.5px;line-height:22.5px;color:#f0f0f0">Lorem ipsum dolor sit amet consectetur. Cursus dolor amet feugiat duis. Mattis sed blandit magna a ornare. Elementum sed sed cras interdum vehicula potenti fringilla. Risus augue pretium elit ullamcorper massa bibendum neque. Justo bibendum neque sed quis.</p>
  <div class="btn" style="left:524px;top:3142px;width:152px;background:var(--white);color:var(--ink)">Contact Us
    <svg viewBox="0 0 12 12"><path d="M2 10L10 2M4 2h6v6" stroke="#7cc242" stroke-width="1.5" fill="none"/></svg></div>
</section>

<section class="testi">
  <div class="abs" style="left:50px;top:72px;font-size:14.5px">Testimonials</div>
  <h2 class="h2 abs" style="left:50px;top:100px;width:440px">What do our customers say about us?</h2>
  <div class="abs" role="img" aria-label="Customer portrait" style="left:69px;top:236px;width:84px;height:84px;border-radius:50%;background:linear-gradient(135deg,#d8cbb8,#8a6a4e)"></div>
  <div class="abs" style="left:50px;top:340px;font-size:15px;font-weight:600">Tobias Lindqvist</div>
  <div class="abs" style="left:50px;top:385px;display:flex;align-items:center;gap:22px;font-size:21px">
    <svg width="26" height="16" viewBox="0 0 26 16"><path d="M25 8H2M8 2L2 8l6 6" stroke="#fff" stroke-width="2" fill="none"/></svg>
    <span>1 / 5</span>
    <svg width="26" height="16" viewBox="0 0 26 16"><path d="M1 8h23M18 2l6 6-6 6" stroke="#fff" stroke-width="2" fill="none"/></svg>
  </div>
  <p class="abs" style="left:427px;top:247px;width:590px;font-size:22px;line-height:30px">“Lorem ipsum dolor sit amet consectetur. Libero tincidunt convallis purus tortor. Orci sem nunc aliquam at fermentum vitae amet. Vitae felis risus vitae vestibulum fringilla vitae felis. Odio ipsum fringilla aliquam elementum iaculis justo consequat amet pharetra.”</p>
</section>

<section class="post">
  <div class="label abs" style="left:67px;top:3856px">Blog</div>
  <h2 class="h2 abs" style="left:67px;top:3887px;width:1000px">Stay Informed with the Latest Trends and Tips in Tree Care</h2>
  <div class="photo" role="img" aria-label="Smartphone showing an app on a patterned surface" style="left:67px;top:3981px;width:338px;height:199px;border-radius:16px;background:linear-gradient(135deg,#8a8a8a,#3a3a3a 60%,#6f6f6f)"></div>
  <div class="photo" role="img" aria-label="Abstract pastel 3D render" style="left:431px;top:3981px;width:338px;height:199px;border-radius:16px;background:linear-gradient(135deg,#b9a3e8,#e7a9d9 55%,#7ad1c8)"></div>
  <div class="photo" role="img" aria-label="Laptop screen on a blue background" style="left:795px;top:3981px;width:338px;height:199px;border-radius:16px;background:linear-gradient(180deg,#1f2f4a,#2f7fc0 70%,#6fb5e6)"></div>
  <p style="left:67px;top:4203px">Lorem ipsum dolor sit amet consectetur. Sed consectetur ut lorem.</p>
  <p style="left:431px;top:4203px">Lorem ipsum dolor sit amet consectetur. Sed consectetur ut lorem.</p>
  <p style="left:795px;top:4203px">Lorem ipsum dolor sit amet consectetur. Sed consectetur ut lorem.</p>
  <a style="left:67px;top:4270px">Read more..</a>
  <a style="left:431px;top:4270px">Read more..</a>
  <a style="left:795px;top:4270px">Read more..</a>
  <div class="btn" style="left:517px;top:4336px;width:166px">See All Blog
    <svg viewBox="0 0 12 12"><path d="M2 10L10 2M4 2h6v6" stroke="#fff" stroke-width="1.5" fill="none"/></svg></div>
</section>

<footer>
  <div class="abs" style="left:67px;top:62px;display:flex;align-items:center;gap:16px">
    <div style="width:56px;height:56px;background:var(--white)"></div>
    <div style="font-size:40px;font-weight:700;letter-spacing:2px">VERDELL</div>
  </div>
  <h4 style="left:518px;top:54px">Links</h4>
  <div class="col abs" style="left:518px;top:87px"><a>Home</a><a>About Us</a><a>Contact</a><a>Services</a></div>
  <h4 style="left:615px;top:54px">Resource</h4>
  <div class="col abs" style="left:615px;top:87px"><a>Blog</a><a>Testimonials</a></div>
  <h4 style="left:734px;top:54px">Subscribe to Our Newsletter</h4>
  <div class="abs" style="left:734px;top:96px;width:399px;height:58px;border:1.5px solid rgba(255,255,255,.5);border-radius:29px;background:rgba(255,255,255,.08)">
    <span class="abs" style="left:16px;top:19px;font-size:13px;color:#e6e6e6">Your Domain (example.com)</span>
    <div class="btn" style="left:266px;top:7px;width:122px;height:42px">Subscribe</div>
  </div>
  <div class="abs" style="left:67px;top:253px;width:1066px;height:1px;background:rgba(255,255,255,.35)"></div>
  <div class="abs" style="left:67px;top:283px;font-size:12px">© 2024 Verdell Tree Care. All rights reserved.</div>
  <div class="social" style="left:993px"></div>
  <div class="social" style="left:1033px"></div>
  <div class="social" style="left:1073px"></div>
  <div class="social" style="left:1113px"></div>
</footer>

</body>
</html>
```